Elevating our current Business Card Design

We want to elevate our current business card with a new design to look like a zenith 300 company. We are a premium lubricant distributor (oil and grease).
We need 2 versions, version 1 is as per the uploaded a copy of our current business card with the English version.
For our Chinese version we need to use the front to be English in English and have the back of the card designed exactly like the front for all info to be in Chinese.
The design template needs to be such that we can amend the template with adding different information for each person's card.
The background colour of the card can be changed- we just need to clearly see all information on the card and logos.
The QJR and Ember steady logos cannot have any colour or display changes- only use the logos attached.
All logos need to be included and all information from the attached current card

```html
<!DOCTYPE html>
<html lang="en">
<head>
<meta charset="utf-8">
<title>Kestrel business card</title>
<link href="https://fonts.googleapis.com/css2?family=Montserrat:wght@400;500;800&display=swap" rel="stylesheet">
<style>
  :root {
    --stage: #1d1d1d;
    --card-white: #ffffff;
    --card-black: #000000;
    --brand-red: #e8302a;
    --brand-grey: #b3b3b6;
    --brand-gold: #f2b12a;
    --ink: #1f1f1f;
    --badge-green: #1f4a3a;
    --badge-grey: #5e5e5e;
  }
  html, body {
    margin: 0;
    padding: 0;
    width: 1200px;
    height: 1059px;
    overflow: hidden;
    background: var(--stage);
    font-family: "Montserrat", sans-serif;
  }
  .canvas { position: relative; width: 1200px; height: 1059px; }
  .card {
    position: absolute;
    border-radius: 22px;
    overflow: hidden;
  }
  .card-front { left: 257px; top: 87px; width: 688px; height: 393px; background: var(--card-white); }
  .card-back { left: 253px; top: 546px; width: 708px; height: 401px; background: var(--card-black); }
  .card-band { position: absolute; left: 0; bottom: 0; width: 100%; height: 20px; }

  .brand-mark {
    position: absolute;
    display: flex;
    align-items: center;
    gap: 10px;
    color: var(--brand-red);
    font-weight: 800;
    letter-spacing: 1px;
    white-space: nowrap;
  }
  .brand-dot { border-radius: 50%; background: var(--brand-gold); flex: none; }
  .front-brand { left: 36px; top: 176px; font-size: 44px; }
  .front-brand .brand-dot { width: 26px; height: 26px; }
  .back-brand { left: 0; right: 0; top: 78px; justify-content: center; font-size: 96px; }
  .back-brand .brand-dot { width: 54px; height: 54px; }

  .divider { position: absolute; left: 320px; top: 76px; width: 2px; height: 244px; background: var(--brand-red); }
  .person-name { position: absolute; left: 338px; top: 76px; margin: 0; font-size: 24px; font-weight: 800; color: var(--brand-red); }
  .person-role { position: absolute; left: 338px; top: 107px; margin: 0; font-size: 14px; color: var(--ink); }
  .address { position: absolute; left: 338px; top: 141px; margin: 0; font-size: 15px; line-height: 18px; color: var(--ink); font-style: normal; }
  .contact-list { position: absolute; left: 338px; top: 197px; margin: 0; padding: 0; list-style: none; }
  .contact-list li { display: flex; align-items: center; height: 24px; font-size: 15px; color: var(--ink); }
  .contact-list svg { width: 18px; height: 18px; margin-right: 16px; flex: none; }

  .partner-badge { position: absolute; }
  .badge-ember { left: 24px; top: 250px; width: 136px; height: 100px; border-radius: 8px; background: var(--badge-green); }
  .badge-partner { left: 173px; top: 290px; width: 336px; height: 48px; border-radius: 6px; background: var(--brand-red); }
  .badge-cert { left: 535px; top: 240px; width: 120px; height: 120px; border-radius: 50%; background: var(--badge-grey); }
</style>
</head>
<body>
<main class="canvas">

  <section class="card card-front" aria-label="Card front">
    <div class="brand-mark front-brand"><span class="brand-dot"></span>KESTREL</div>
    <div class="divider"></div>
    <h1 class="person-name">Maren Castell</h1>
    <p class="person-role">Administraction Executive</p>
    <address class="address">48 Freight Parade<br>harlow, WA 6210</address>
    <ul class="contact-list">
      <li><svg viewBox="0 0 20 20"><path fill="#e8302a" d="M2 7c0-3 4-4 8-4s8 1 8 4v2h-4V7H6v2H2zM4 10h12l1 7H3z"/><circle cx="10" cy="13.5" r="2" fill="#fff"/></svg>1300 472 615</li>
      <li><svg viewBox="0 0 20 20"><rect x="5" y="1" width="10" height="18" rx="2" fill="#e8302a"/><rect x="6.5" y="3" width="7" height="12" fill="#fff"/></svg>+16 412 778 309</li>
      <li><svg viewBox="0 0 20 20"><rect x="5" y="2" width="10" height="5" fill="#e8302a"/><rect x="2" y="7" width="16" height="8" rx="2" fill="#e8302a"/><rect x="5" y="12" width="10" height="6" fill="#fff" stroke="#e8302a" stroke-width="1.5"/></svg>+16 8 9204 5561</li>
      <li><svg viewBox="0 0 20 20"><rect x="1" y="4" width="18" height="12" fill="#e8302a"/><path d="M1 4l9 7 9-7" fill="none" stroke="#fff" stroke-width="1.5"/></svg>maren.castell@kestreldirect.com</li>
      <li><svg viewBox="0 0 20 20"><circle cx="10" cy="10" r="9" fill="#e8302a"/><path d="M1 10h18M10 1v18" fill="none" stroke="#fff" stroke-width="1.5"/></svg>www.kestreldirect.com</li>
    </ul>
    <svg class="card-band" viewBox="0 0 688 20" preserveAspectRatio="none" aria-hidden="true">
      <polygon points="0,0 331,0 313,20 0,20" fill="var(--brand-red)"/>
      <polygon points="338,0 688,0 688,20 320,20" fill="var(--brand-grey)"/>
    </svg>
  </section>

  <section class="card card-back" aria-label="Card back">
    <div class="brand-mark back-brand"><span class="brand-dot"></span>KESTREL</div>

    <div class="partner-badge badge-ember" role="img" aria-label="Ember steady network member badge"></div>
    <div class="partner-badge badge-partner" role="img" aria-label="Partner distributor badge"></div>
    <div class="partner-badge badge-cert" role="img" aria-label="QJR ISO system certification badge"></div>

    <svg class="card-band" viewBox="0 0 708 20" preserveAspectRatio="none" aria-hidden="true">
      <polygon points="0,0 341,0 323,20 0,20" fill="var(--brand-red)"/>
      <polygon points="348,0 708,0 708,20 330,20" fill="var(--brand-grey)"/>
    </svg>
  </section>

</main>
</body>
</html>
```